New Property development signage

large poster for a new development.
3 metres x 2 metres. To include the following.

Tresswick Gardens
TO LET
LUXURY FULLY FURNISHED LARGE
2 AND 3 BED APARTMENTS
Garrold Estates
362 4150
www.garroldestates-example.com

Need this to be large simple writing with Garrold estates logo on the bottom

Target Market(s)

High end rental property market

Industry/Entity Type

Real Estate Development

Colors
000000
cbcbcb
0555a3

Requirements
Must have
• Name of the development must be in a different font, classic style
Nice to have
• Light Grey background, blues for colours
Should not have
• anymore than 3 /4 colours

```html
<!DOCTYPE html>
<html lang="en">
<head>
<meta charset="utf-8">
<title>Tresswick Gardens – To Let</title>
<link rel="stylesheet" href="https://fonts.googleapis.com/css2?family=Great+Vibes&family=Tinos:wght@700&display=swap">
<style>
  :root {
    --bg-grey: #cbcbcb;
    --brand-blue: #0555a3;
    --ink: #000000;
    --frame: #ffffff;
  }
  * { margin: 0; padding: 0; box-sizing: border-box; }
  html, body { width: 800px; height: 1200px; overflow: hidden; }
  body { background: var(--bg-grey); }
  .poster {
    position: relative;
    width: 800px;
    height: 1200px;
    background: var(--bg-grey);
    color: var(--brand-blue);
    font-family: "Tinos", "Times New Roman", serif;
    font-weight: 700;
    text-align: center;
  }
  .development-name {
    position: absolute;
    top: 52px; left: 0; width: 100%;
    font-family: "Great Vibes", cursive;
    font-weight: 400;
    font-size: 92px;
    line-height: 1;
  }
  .status {
    position: absolute;
    top: 168px; left: 0; width: 100%;
    font-size: 38px;
    letter-spacing: 1px;
  }
  .gallery {
    position: absolute;
    top: 282px; left: 134px;
    width: 532px; height: 264px;
    display: grid;
    grid-template-columns: repeat(3, 1fr);
    grid-template-rows: repeat(2, 1fr);
    gap: 4px;
  }
  .gallery-photo { border: 2px solid var(--frame); }
  .photo-kitchen  { background: linear-gradient(135deg, #e9e4dc, #8a5a3a); }
  .photo-living   { background: linear-gradient(135deg, #6fa9c9, #5a3b2a); }
  .photo-lounge   { background: linear-gradient(135deg, #f1ece2, #a06a3e); }
  .photo-bedroom  { background: linear-gradient(135deg, #d9d3c6, #3f5d9a); }
  .photo-dining   { background: linear-gradient(135deg, #e6ddcf, #7a5236); }
  .photo-bedroom2 { background: linear-gradient(135deg, #ece6da, #4a66a8); }
  .offer {
    position: absolute;
    top: 682px; left: 0; width: 100%;
    font-size: 43px;
    line-height: 52px;
    transform: scaleX(0.92);
  }
  .phone {
    position: absolute;
    top: 826px; left: 0; width: 100%;
    font-size: 56px;
    letter-spacing: 2px;
  }
  .agent-name {
    position: absolute;
    top: 935px; left: 0; width: 100%;
    font-size: 60px;
    line-height: 1;
  }
  .website {
    position: absolute;
    top: 1064px; left: 0; width: 100%;
    font-size: 33px;
  }
</style>
</head>
<body>
  <main class="poster">
    <h1 class="development-name">Tresswick Gardens</h1>
    <p class="status">TO LET</p>

    <section class="gallery">
      <div class="gallery-photo photo-kitchen" role="img" aria-label="Fitted kitchen with wood cabinets"></div>
      <div class="gallery-photo photo-living" role="img" aria-label="Living room with window and sofa"></div>
      <div class="gallery-photo photo-lounge" role="img" aria-label="Bright lounge with armchairs"></div>
      <div class="gallery-photo photo-bedroom" role="img" aria-label="Bedroom with double bed and wardrobe"></div>
      <div class="gallery-photo photo-dining" role="img" aria-label="Open plan living and dining area"></div>
      <div class="gallery-photo photo-bedroom2" role="img" aria-label="Second bedroom with blue bedding"></div>
    </section>

    <p class="offer">LUXURY FULLY FURNISHED LARGE<br>2 AND 3 BED APARTMENTS</p>
    <p class="phone">362 4150</p>
    <p class="agent-name">Garrold Estates</p>
    <p class="website">www.garroldestates-example.com</p>
  </main>
</body>
</html>
```